Coffee Bag Design for Tollbury Coffee

We’re excited to invite you to help us bring Tollbury Coffee to life on grocery store shelves with a design that embodies our mission of spreading goodness and creating a lasting impact. Tollbury Coffee represents warmth, positivity, and the power of small actions to create ripples of goodness. Each cup not only offers a rich, gourmet coffee experience but also gives back to the community, with $2 from each bag supporting local food banks.

To reflect this vision, we’d love for the design to feature a dark (greyish) blue as the base color to convey depth and quality, complemented by a vibrant light blue that will catch the eye and add energy. Tan or gold accents could add an elegant touch and a feeling of warmth. We are aiming for a look that feels uplifting and engaging, with simplicity and elegance, yet stands out amid other brands on the shelf.

I am attaching the dimension of the bag.

Other information that needs to be listed:
Ingredients: 100% Arabica Coffee
Net Wt. 12 oz. (340 g)
Roasted and distributed by:
Name
Address
email

Text on the back of the bag:
Tollbury Coffee is crafted with a belief that kindness and positivity can spread, touching countless lives with every sip. This gourmet blend delivers a rich taste experience while giving back, as $2 from each bag sold is donated to local food banks to help those in need. Enjoy the warmth and goodness in each cup, knowing you’re making a difference with every purchase.

Thank you!

```html
<!DOCTYPE html>
<html lang="en">
<head>
<meta charset="utf-8">
<title>Tollbury Coffee – Bag Front</title>
<link rel="stylesheet" href="https://fonts.googleapis.com/css2?family=Poppins:ital,wght@0,300;0,400;0,500;0,600;0,700;1,400;1,600&family=Roboto+Condensed:wght@700&display=swap">
<style>
  :root {
    --backdrop: #e2e2e2;
    --navy: #14223f;
    --navy-deep: #0d1629;
    --sky: #2f8fd6;
    --sky-light: #5fb3ec;
    --gold: #d8b65e;
    --gold-light: #f0d98f;
    --cream: #efe6d2;
    --ink: #1b2a4a;
    --roast: #6b4426;
  }
  * { box-sizing: border-box; margin: 0; padding: 0; }
  html, body { width: 1200px; height: 933px; overflow: hidden; }
  body {
    background: var(--backdrop);
    font-family: "Poppins", sans-serif;
    color: var(--ink);
    position: relative;
  }
  .bag-front {
    position: absolute;
    left: 340px; top: 22px;
    width: 520px; height: 890px;
    border-radius: 10px 10px 4px 4px;
    overflow: hidden;
    background: radial-gradient(ellipse at 50% 40%, #1c2f55 0%, var(--navy) 55%, var(--navy-deep) 100%);
  }
  .center-band {
    position: absolute;
    left: 155px; top: 0;
    width: 210px; height: 100%;
    background: linear-gradient(90deg, #1f72b8 0%, var(--sky-light) 50%, #1f72b8 100%);
    border-left: 8px solid var(--gold);
    border-right: 8px solid var(--gold);
  }
  .center-band::before, .center-band::after {
    content: "";
    position: absolute; top: 0; bottom: 0;
    width: 2px; background: var(--gold-light);
  }
  .center-band::before { left: 6px; }
  .center-band::after { right: 6px; }
  .brand-seal {
    position: absolute;
    left: 115px; top: 230px;
    width: 290px; height: 230px;
    border-radius: 50%;
    background: var(--navy-deep);
    border: 3px solid var(--gold);
    display: flex; align-items: center; justify-content: center;
  }
  .brand-seal__name {
    font-weight: 500;
    font-size: 34px;
    line-height: 1.1;
    color: var(--gold);
    text-align: center;
  }
  .info-label {
    position: absolute;
    left: 40px; top: 560px;
    width: 440px; height: 270px;
    background: var(--cream);
    box-shadow: 0 2px 6px rgba(0,0,0,.35);
  }
  .info-label__brand {
    position: absolute; left: 20px; top: 20px;
    font-size: 18px; font-weight: 500; line-height: 1.05;
  }
  .info-label__origin-line {
    position: absolute; left: 180px; top: 52px;
    font-size: 14px; font-weight: 300;
  }
  .info-label__seal {
    position: absolute; right: 22px; top: 12px;
    width: 62px; height: 62px;
    border-radius: 50%;
    border: 2px solid var(--ink);
  }
  .info-label__quote {
    position: absolute; left: 20px; top: 82px;
    width: 155px;
    font-size: 8.5px; font-style: italic; line-height: 1.35;
    text-align: center;
    border-top: 1px solid var(--ink);
    padding-top: 6px;
  }
  .tab-row {
    position: absolute;
    display: flex; align-items: stretch;
  }
  .tab-row__tab {
    width: 16px;
    background: var(--navy);
    color: var(--cream);
    font-size: 7px; letter-spacing: 1px;
    writing-mode: vertical-rl; transform: rotate(180deg);
    display: flex; align-items: center; justify-content: center;
  }
  .notes-row { left: 20px; top: 165px; width: 160px; height: 50px; border-bottom: 1px solid var(--ink); }
  .notes-row__text {
    font-size: 11px; font-weight: 600; font-style: italic; line-height: 1.3;
    padding: 6px 0 0 8px;
  }
  .origin-box {
    position: absolute; left: 188px; top: 82px;
    width: 232px; height: 66px;
    background: linear-gradient(90deg, var(--navy-deep), var(--navy));
    color: #fff; text-align: center;
    font-family: "Roboto Condensed", sans-serif; font-weight: 700;
    padding-top: 6px;
  }
  .origin-box__country { font-size: 29px; letter-spacing: 1px; line-height: 1.1; }
  .origin-box__farm { font-size: 13px; letter-spacing: 1px; }
  .roast-row { left: 188px; top: 156px; width: 232px; height: 60px; border-left: 1px solid var(--ink); }
  .roast-scale { display: flex; justify-content: space-around; flex: 1; padding-top: 6px; }
  .roast-scale__step { display: flex; flex-direction: column; align-items: center; width: 42px; }
  .roast-scale__step svg { width: 28px; height: 26px; }
  .roast-scale__label { font-size: 6px; color: var(--roast); text-align: center; line-height: 1.1; margin-top: 2px; font-weight: 500; }
  .info-label__product {
    position: absolute; left: 20px; top: 222px;
    font-size: 13px; line-height: 1.5;
  }
  .info-label__product strong { font-weight: 700; }
  .info-label__method {
    position: absolute; left: 190px; top: 222px;
    font-size: 11px; font-weight: 600; line-height: 1.2;
  }
  .info-label__weight {
    position: absolute; right: 20px; top: 222px;
    font-size: 14px; font-weight: 700; text-align: right; line-height: 1.5;
  }
  .info-label__rule {
    position: absolute; left: 20px; right: 20px; top: 218px;
    border-top: 1px solid var(--ink);
  }
</style>
</head>
<body>
  <div class="bag-front" role="img" aria-label="Dark navy bag front with gold-outlined fan scale pattern">
    <div class="center-band" role="img" aria-label="Light blue band with fine woven texture"></div>

    <div class="brand-seal">
      <p class="brand-seal__name">Tollbury<br>Coffee</p>
    </div>

    <section class="info-label">
      <p class="info-label__brand">Tollbury<br>Coffee</p>
      <p class="info-label__origin-line">100% Arabica Coffee</p>
      <div class="info-label__seal"></div>

      <p class="info-label__quote">"Fruity Aroma, Long Sweet Finish, Structured Acidity, Juicy And Silky Mouthfeel, Flavour Note of Apricot, Caramel, Mixed Berries And Chocolate"</p>

      <div class="tab-row notes-row">
        <span class="tab-row__tab">NOTES</span>
        <p class="notes-row__text">Mixed Berries And Chocolate, Caramel</p>
      </div>

      <div class="origin-box">
        <p class="origin-box__country">COSTA RICA</p>
        <p class="origin-box__farm">HACIENDA VERLANA</p>
      </div>

      <div class="tab-row roast-row">
        <span class="tab-row__tab">ROAST</span>
        <div class="roast-scale">
          <div class="roast-scale__step"><svg viewBox="0 0 28 26"><path d="M4 8h16v10a5 5 0 0 1-5 5H9a5 5 0 0 1-5-5z" fill="none" stroke="#6b4426" stroke-width="1.6"/><path d="M20 11h3a3 3 0 0 1 0 6h-3" fill="none" stroke="#6b4426" stroke-width="1.6"/><path d="M12 2c-2 2 2 3 0 5" fill="none" stroke="#6b4426" stroke-width="1.2"/></svg><span class="roast-scale__label">LIGHT</span></div>
          <div class="roast-scale__step"><svg viewBox="0 0 28 26"><path d="M4 8h16v10a5 5 0 0 1-5 5H9a5 5 0 0 1-5-5z" fill="none" stroke="#6b4426" stroke-width="1.6"/><path d="M20 11h3a3 3 0 0 1 0 6h-3" fill="none" stroke="#6b4426" stroke-width="1.6"/><path d="M12 2c-2 2 2 3 0 5" fill="none" stroke="#6b4426" stroke-width="1.2"/></svg><span class="roast-scale__label">LIGHT<br>MEDIUM</span></div>
          <div class="roast-scale__step"><svg viewBox="0 0 28 26"><path d="M4 8h16v10a5 5 0 0 1-5 5H9a5 5 0 0 1-5-5z" fill="none" stroke="#6b4426" stroke-width="1.6"/><path d="M20 11h3a3 3 0 0 1 0 6h-3" fill="none" stroke="#6b4426" stroke-width="1.6"/><path d="M12 2c-2 2 2 3 0 5" fill="none" stroke="#6b4426" stroke-width="1.2"/></svg><span class="roast-scale__label">MEDIUM</span></div>
          <div class="roast-scale__step"><svg viewBox="0 0 28 26"><path d="M4 8h16v10a5 5 0 0 1-5 5H9a5 5 0 0 1-5-5z" fill="#6b4426" stroke="#6b4426" stroke-width="1.6"/><path d="M20 11h3a3 3 0 0 1 0 6h-3" fill="none" stroke="#6b4426" stroke-width="1.6"/><path d="M12 2c-2 2 2 3 0 5" fill="none" stroke="#6b4426" stroke-width="1.2"/></svg><span class="roast-scale__label">MEDIUM<br>DARK</span></div>
          <div class="roast-scale__step"><svg viewBox="0 0 28 26"><path d="M4 8h16v10a5 5 0 0 1-5 5H9a5 5 0 0 1-5-5z" fill="none" stroke="#6b4426" stroke-width="1.6"/><path d="M20 11h3a3 3 0 0 1 0 6h-3" fill="none" stroke="#6b4426" stroke-width="1.6"/><path d="M12 2c-2 2 2 3 0 5" fill="none" stroke="#6b4426" stroke-width="1.2"/></svg><span class="roast-scale__label">DARK</span></div>
        </div>
      </div>

      <div class="info-label__rule"></div>
      <p class="info-label__product"><strong>Roasted</strong> coffee<br><strong>Whole</strong> bean</p>
      <p class="info-label__method">Traditional<br>Natural<br>Method</p>
      <p class="info-label__weight">Net Wt.<br>12 oz. (340 g)</p>
    </section>
  </div>
</body>
</html>
```